EVENT TENT DESIGN/ Revamping our Bi-fold Brochure/ Creating Tri Fold Brochure

Hello, I uploaded a pdf that shows the breakdown of our current brochure. We are having a hard time getting the colors correct. We want the front and back as well as any other gradient areas to be closer to our colors on the "Lumera Color Code and Font" document we uploaded.

We also feel like the solar images, outdated or the colors are a little too dull. We want more modern images with panels that are black on black or very very very navy/black blue worst case scenario.

In addition, we feel as the though some of the fonts and banners feel a little basic.

We are looking for somebody to add that modern feel to the brochure as well as turn the information into a trifold.

I will be uploading the brand page with colors and fonts, our logo, and the current book we have made. thank you in advance.

Lastly we need a "Refer a Friend" Page in the brochure. Please use the below link for inspiration. We are currently running a promo on our website, on our Brochure we like the referral pay out as follows.
https://www.trybrevaxenergy.com/refer-a-friend
You receive $35 for each qualified friend. Your qualified friend will get $25.
Get $500 when they go solar; $250 when they get a new roof.!

here is a link to our website. www.trybrevaxenergy.com
______________________________________________

Hello I increased the Winnings so that i can increase the scope of the project. I am uploading the tent measurements and a base template for you to work with. If you are a designer and have already created a Brochure for me and your design hasn't been deleted that means you are in the running for the winnings. I would like you to apply those elements to the tent design.

If you are a new designer. Use the elements that i want for the brochure and trifold and apply that to a Tent design.

my goal is to pick a designer by EOBD Thursday Aug 24th, 2023. Thank you

Colors
E54698
E96AAD
F1A4CE
F9D9EA
FCEFF6
A7469A
B969AE
D3A5CF
EDDBEB
F8F0F9
6B429C
8869AF
B7A5CE
E3DAEB
F3F0F8

Requirements
Must have
• Bi Fold Brochure Design, Tri-Fold Brochure, Event Tent Design

```html
<!DOCTYPE html>
<html lang="en">
<head>
<meta charset="utf-8">
<title>Lumera Event Tent – Back Wall</title>
<link href="https://fonts.googleapis.com/css2?family=Russo+One&family=Michroma&family=Montserrat:wght@300;400;600&display=swap" rel="stylesheet">
<style>
  :root{
    --magenta:#e41ff0;
    --violet:#8a12f2;
    --purple-text:#a915ef;
    --ink:#3d3d44;
    --card-fill:rgba(255,255,255,.86);
    --sky-light:#f4f8fc;
    --sky-blue:#8fc4e6;
    --panel-grey:#8d939b;
    --page:#ffffff;
  }
  *{margin:0;padding:0;box-sizing:border-box}
  html,body{width:849px;height:1200px;overflow:hidden;background:var(--page)}
  body{position:relative;font-family:"Montserrat",sans-serif;color:var(--ink)}

  .back-wall{position:absolute;left:20px;top:316px;width:809px;height:568px;overflow:hidden}
  .backdrop{position:absolute;inset:0;
    background:
      radial-gradient(ellipse 60% 55% at 15% 25%, rgba(255,255,255,.95), rgba(255,255,255,0) 70%),
      linear-gradient(165deg, var(--sky-light) 0%, #d6e9f6 30%, var(--sky-blue) 55%, #c9ced4 70%, var(--panel-grey) 100%);}

  .why-title{position:absolute;left:43px;top:48px;font-family:"Russo One",sans-serif;font-size:29px;line-height:36px;
    background:linear-gradient(90deg,var(--magenta),var(--violet));-webkit-background-clip:text;background-clip:text;color:transparent}
  .why-list{position:absolute;left:43px;top:128px;width:220px;list-style:none;font-weight:300;font-size:15px;line-height:19px;color:#33333a}
  .why-list li{position:relative;padding-left:7px;margin-bottom:9.5px}
  .why-list li::before{content:"·";position:absolute;left:0;top:0}

  .warranty-badge{position:absolute;left:84px;top:414px;width:116px;height:129px}

  .site-url{position:absolute;left:317px;top:28px;width:440px;font-family:"Michroma",sans-serif;font-size:18px;letter-spacing:0;white-space:nowrap;color:#3a3a40}
  .column-heading{position:absolute;top:59px;font-family:"Russo One",sans-serif;font-size:16px;color:var(--purple-text);letter-spacing:.3px}
  .column-heading.panels{left:300px}
  .column-heading.storage{left:579px}

  .feature-card{position:absolute;width:233px;height:100px;border:2px solid var(--violet);border-radius:14px;background:var(--card-fill);overflow:hidden}
  .feature-card .icon{position:absolute;left:14px;top:13px;width:70px;height:70px;border-radius:11px;
    background:linear-gradient(135deg,var(--magenta),var(--violet));display:flex;align-items:center;justify-content:center}
  .feature-card .icon svg{width:44px;height:44px;fill:none;stroke:#fff;stroke-width:2.2;stroke-linecap:round;stroke-linejoin:round}
  .feature-card h3{position:absolute;left:96px;top:10px;font-family:"Russo One",sans-serif;font-weight:400;font-size:23px;line-height:26px;
    background:linear-gradient(90deg,var(--magenta),var(--violet));-webkit-background-clip:text;background-clip:text;color:transparent}
  .feature-card p{position:absolute;left:96px;top:41px;right:6px;font-size:9.6px;line-height:11.2px;color:#4a4a52}
  .feature-card .sub{position:absolute;left:94px;top:35px;font-family:"Russo One",sans-serif;font-size:8px;color:var(--purple-text);white-space:nowrap}
  .feature-card.tight h3{top:7px}
  .feature-card.tight p{top:46px;left:94px;right:4px;font-size:8.2px;line-height:9px}

  .col-a{left:288px}
  .col-b{left:546px}
  .row-1{top:88px}
  .row-2{top:203px}
  .row-3{top:317px}
  .row-4{top:432px}
</style>
</head>
<body>
<section class="back-wall">
  <div class="backdrop" role="img" aria-label="Photo of a bright blue sky over dark rooftop solar panels"></div>

  <h1 class="why-title">WHY<br>CHOOSE US?</h1>
  <ul class="why-list">
    <li>Accredited professionals</li>
    <li>We use high-quality products with the best warranties</li>
    <li>Highly credited installers and professionals</li>
    <li>Fully licensed and insured</li>
    <li>Devoted customer service that you can rely on</li>
    <li>Quick and easy process from start to finish</li>
  </ul>

  <svg class="warranty-badge" viewBox="0 0 116 129" aria-label="25 years warranty">
    <defs>
      <linearGradient id="badgeFill" x1="0" y1="0" x2="0" y2="1">
        <stop offset="0" stop-color="#e41ff0"/><stop offset="1" stop-color="#8a12f2"/>
      </linearGradient>
    </defs>
    <path d="M58 2 L112 30 Q115 32 115 36 L115 93 Q115 97 112 99 L58 127 L4 99 Q1 97 1 93 L1 36 Q1 32 4 30 Z" fill="url(#badgeFill)"/>
    <rect x="1" y="44" width="114" height="38" fill="#fff"/>
    <text x="58" y="72" text-anchor="middle" font-family="Russo One, sans-serif" fill="#a915ef">
      <tspan font-size="26">25</tspan><tspan font-size="16" dx="3">YEARS</tspan>
    </text>
    <text x="58" y="97" text-anchor="middle" font-family="Russo One, sans-serif" font-size="8.5" fill="#fff" letter-spacing="1">• WARRANTY •</text>
  </svg>

  <div class="site-url">WWW.TRYBREVAXENERGY.COM</div>
  <h2 class="column-heading panels">OUR SOLAR PANELS</h2>
  <h2 class="column-heading storage">SOLAR STORAGE</h2>

  <article class="feature-card col-a row-1">
    <div class="icon"><svg viewBox="0 0 44 44"><path d="M5 22 L22 8 L39 22"/><path d="M9 19 V38 H35 V19"/><rect x="12" y="26" width="9" height="6"/><path d="M26 38 V27 H31 V38"/><path d="M12 13 L20 7"/></svg></div>
    <h3>Output</h3>
    <p>We guarantee that our high-performance panels will deliver the promised quantity of power.</p>
  </article>

  <article class="feature-card col-a row-2">
    <div class="icon"><svg viewBox="0 0 44 44"><circle cx="22" cy="22" r="18"/><circle cx="22" cy="22" r="12"/><path d="M22 15 L24 20 L29 20 L25 23.5 L26.5 28.5 L22 25.5 L17.5 28.5 L19 23.5 L15 20 L20 20 Z"/></svg></div>
    <h3>Quality</h3>
    <p>Our panel partners are hand-selected to deliver you the finest, from materials to efficiency.</p>
  </article>

  <article class="feature-card col-a row-3">
    <div class="icon"><svg viewBox="0 0 44 44"><path d="M22 4 L37 10 V22 Q37 34 22 40 Q7 34 7 22 V10 Z"/><path d="M15 22 L20 27 L29 17"/></svg></div>
    <h3>Warranty</h3>
    <p>Your panels will each be covered by performance and product warranties.</p>
  </article>

  <article class="feature-card col-a row-4 tight">
    <div class="icon"><svg viewBox="0 0 44 44"><path d="M9 8 H38 L35 30 H6 Z"/><path d="M8 15 H37 M7 22 H36 M16 8 L14 30 M26 8 L24 30"/><path d="M20 30 V36 M14 38 H28"/></svg></div>
    <h3>25-Year</h3>
    <span class="sub">Panel Manufacturer Warranty</span>
    <p>We ensure that product and performance warranties reflect our commitment to making durable, high-quality panels.</p>
  </article>

  <article class="feature-card col-b row-1">
    <div class="icon"><svg viewBox="0 0 44 44"><path d="M22 4 L37 10 V22 Q37 34 22 40 Q7 34 7 22 V10 Z"/></svg></div>
    <h3>Protection</h3>
    <p>Using the saved energy, your home is safeguarded during a power loss.</p>
  </article>

  <article class="feature-card col-b row-2">
    <div class="icon"><svg viewBox="0 0 44 44"><rect x="13" y="7" width="18" height="33" rx="2"/><path d="M18 4 H26"/><path d="M17 14 H27 M17 20 H27 M17 26 H27 M17 32 H27"/></svg></div>
    <h3>Storage</h3>
    <p>Put any extra solar power in your battery rather than transferring it to the grid.</p>
  </article>

  <article class="feature-card col-b row-3">
    <div class="icon"><svg viewBox="0 0 44 44"><rect x="10" y="5" width="24" height="34" rx="2"/><rect x="14" y="9" width="16" height="26"/><path d="M18 22 L21 25 L26 19"/></svg></div>
    <h3>Monitor</h3>
    <p>Use the Voltaro or Ampyra app-lications to monitor and manage your home's energy usage.</p>
  </article>

  <article class="feature-card col-b row-4">
    <div class="icon"><svg viewBox="0 0 44 44"><circle cx="22" cy="22" r="10"/><path d="M22 4 V8 M22 36 V40 M4 22 H8 M36 22 H40 M9 9 L12 12 M32 32 L35 35 M9 35 L12 32 M32 12 L35 9"/><path d="M25 36 Q31 26 38 32 Q32 38 25 36 Z"/></svg></div>
    <h3>Power</h3>
    <p>Your home is capable of running entirely off the grid and using solar energy.</p>
  </article>
</section>
</body>
</html>
```